Luxury Wine Label for New Startup Winery

We need a wine label for our new winery startup. We have worked with a local designer but do not feel the resulting label / logo have the elevation required to present our brand as a luxury wine. Our winery is called "Quailbrook Vineyards" and we are focused on extremely high quality hand crafted artisan and estate wines from the Pacific Northwest.
We would like to see designs that utilize a tree line, or other imagery that represents the "Quailbrook" part of our company name. Another interesting feature could be wood grain.
A logo will be required based on your design so please design with this in mind:
This logo should be consistent with the wine bottle label design, and should be representative of our high end exclusive wine while giving a sense of place (Oregon/ Pacific Northwest.)
I will supply an image of the design we received from our local designer, PLEASE NOTE: in general we do like wood grain and tree line concepts but feel the execution was poorly done.
ATTN: Logo design should be suitable for use on: Bottles (Red wine/rose/white wine), Bussiness cards, vehicle signage, business signage, etc
P.S.:
If you have a design that is not outside the box we are still interested in seeing it.
Label is for a burgundy style bottle with a label height of 3.5 - 4" and a width of 3.5-4"
any label <= 4"x4" and >=3.5"x3.5" will be acceptable:
HOWEVER Width should be greater than or equal to height due to the bottle format
Target Market(s)
Wine enthusiasts with adequate discretionary budgets to afford $100 bottles of wine.
Industry/Entity Type
Wine / Winery
Requirements
Must have
- A sense of luxury, a feel of exclusivity, and a theme consistent with our product and brand name
Nice to have
- Tree line, wood grain or other wood themes. Serif fonts
Should not have
- anything cheesy, off topic, hard to read script fonts or anything that makes the label hard to read from a few feet away or too busy

```html
<!DOCTYPE html>
<html lang="en">
<head>
<meta charset="utf-8">
<title>Quailbrook Vineyards – Syrah Label</title>
<link rel="stylesheet" href="https://fonts.googleapis.com/css2?family=Cormorant+Garamond:ital,wght@0,700;1,500&family=Lexend+Exa:wght@400&display=swap">
<style>
  :root {
    --page: #ffffff;
    --label-black: #050001;
    --wine-deep: #120003;
    --wine-mid: #3a0409;
    --wine-glow: #6b0a17;
    --gold: #c6ae76;
    --wood-dark: #2a140a;
    --wood-mid: #6b3519;
    --wood-light: #a9622e;
  }
  * { margin: 0; padding: 0; box-sizing: border-box; }
  html, body {
    width: 1200px;
    height: 866px;
    overflow: hidden;
    background: var(--page);
  }
  .canvas {
    position: relative;
    width: 1200px;
    height: 866px;
    display: flex;
    align-items: center;
    justify-content: center;
  }
  .wine-label {
    position: relative;
    width: 660px;
    height: 660px;
    background: var(--label-black);
    overflow: hidden;
  }
  .label-art {
    position: absolute;
    inset: 0;
    width: 100%;
    height: 100%;
  }
  .label-text {
    position: absolute;
    left: 0;
    width: 100%;
    text-align: center;
    color: var(--gold);
  }
  .winery-name {
    top: 92px;
    font-family: "Cormorant Garamond", Georgia, serif;
    font-weight: 700;
    font-size: 47px;
    line-height: 53px;
    letter-spacing: 0.5px;
    text-transform: uppercase;
  }
  .varietal {
    top: 205px;
    font-family: "Cormorant Garamond", Georgia, serif;
    font-style: italic;
    font-weight: 500;
    font-size: 215px;
    line-height: 230px;
    letter-spacing: -2px;
  }
  .vintage {
    top: 548px;
    font-family: "Lexend Exa", Arial, sans-serif;
    font-size: 27px;
    line-height: 34px;
    letter-spacing: 2px;
  }
  .region {
    top: 594px;
    font-family: "Lexend Exa", Arial, sans-serif;
    font-size: 16px;
    line-height: 22px;
    letter-spacing: 1.5px;
    text-transform: uppercase;
  }
</style>
</head>
<body>
<main class="canvas">
  <section class="wine-label">
    <svg class="label-art" viewBox="0 0 660 660" xmlns="http://www.w3.org/2000/svg">
      <defs>
        <radialGradient id="wine-field" cx="0.44" cy="0.5" r="0.62">
          <stop offset="0" stop-color="var(--wine-glow)"/>
          <stop offset="0.55" stop-color="var(--wine-mid)"/>
          <stop offset="1" stop-color="var(--wine-deep)"/>
        </radialGradient>
        <linearGradient id="wood-tone-top" x1="0" y1="0" x2="1" y2="1">
          <stop offset="0" stop-color="var(--wood-mid)"/>
          <stop offset="0.5" stop-color="var(--wood-light)"/>
          <stop offset="1" stop-color="var(--wood-dark)"/>
        </linearGradient>
        <linearGradient id="wood-tone-bottom" x1="0" y1="0" x2="1" y2="1">
          <stop offset="0" stop-color="var(--wood-dark)"/>
          <stop offset="0.45" stop-color="var(--wood-light)"/>
          <stop offset="1" stop-color="var(--wood-mid)"/>
        </linearGradient>
      </defs>
      <rect class="label-field" x="16" y="16" width="628" height="628" fill="url(#wine-field)"/>
      <path class="wood-grain-top" role="img" aria-label="Wood grain texture sweeping in from the top left corner"
            fill="url(#wood-tone-top)"
            d="M0 0 H285 C265 40 240 70 210 110 C180 150 160 175 110 195 C75 210 65 240 60 290 C56 330 55 380 30 400 C18 410 8 415 0 420 Z"/>
      <path class="wood-grain-bottom" role="img" aria-label="Wood grain texture sweeping in from the bottom right corner"
            fill="url(#wood-tone-bottom)"
            d="M660 210 V660 H345 C400 640 420 620 430 590 C438 560 440 520 470 500 C510 475 535 440 555 395 C575 350 600 320 630 290 C645 270 652 240 660 210 Z"/>
      <rect class="gold-frame" x="17" y="17" width="626" height="626" fill="none" stroke="var(--gold)" stroke-width="4"/>
    </svg>
    <h1 class="label-text winery-name">Quailbrook<br>Vineyards</h1>
    <p class="label-text varietal">Syrah</p>
    <p class="label-text vintage">2024</p>
    <p class="label-text region">Willamette Valley</p>
  </section>
</main>
</body>
</html>
```